New Innovative Counselling and psychotherapy Service needs Business Card design

Keep it simple and professional. On one side, just company name and logo (perhaps in all blue) and maybe a tag line.

On other side (all white) my name and Qualifications in centre

Industry/Entity Type

Health And Wellness

Contact Information for Business Card

Dara Whelby
Counsellor & Psychotherapist
BSc (Psychol.), BA, Dip. (Couns. & Psych.), PG.Cert (CBT), FGTrK, ONRE

I will also require Mobile no, Email and web site address of which I'll pass on to final designer.

Font styles to use
Sans Serif

Requirements
Must have
• My Logo Only and please use the colours in logo that is in it.
Should not have
• Any other images

```html
<!DOCTYPE html>
<html lang="en">
<head>
<meta charset="utf-8">
<title>Harbour Lane – Business Card</title>
<link rel="stylesheet" href="https://fonts.googleapis.com/css2?family=Montserrat:wght@400&family=Roboto:wght@400;700&display=swap">
<style>
  :root {
    --page: #e9e9ea;
    --card-white: #fbfbfb;
    --brand-blue: #47a8e0;
    --brand-teal: #6cc0c8;
    --brand-green: #93d06a;
    --ink: #2b2b2b;
    --ink-soft: #444;
  }
  * { box-sizing: border-box; margin: 0; padding: 0; }
  html, body { width: 1200px; height: 726px; overflow: hidden; background: var(--page); }
  .canvas {
    position: relative; width: 1200px; height: 726px;
    display: flex; align-items: center; justify-content: center; gap: 40px;
  }
  .card {
    position: relative; width: 540px; height: 309px;
    border-radius: 4px; overflow: hidden;
    box-shadow: 0 2px 6px rgba(0,0,0,.12);
  }
  /* Front */
  .card-front {
    background: linear-gradient(120deg, var(--brand-blue) 0%, var(--brand-teal) 45%, var(--brand-green) 100%);
    display: flex; align-items: center; justify-content: center;
  }
  .card-front .decor { position: absolute; inset: 0; }
  .card-front .company {
    position: relative;
    font-family: "Montserrat", sans-serif; font-weight: 400;
    font-size: 44px; letter-spacing: 1px; color: #fff;
  }
  /* Back */
  .card-back { background: var(--card-white); }
  .tab {
    position: absolute; width: 22px; height: 150px;
    background: var(--brand-blue); border-radius: 11px;
  }
  .tab-left { left: -11px; bottom: -40px; }
  .tab-right { right: -11px; top: -40px; }
  .brand {
    position: absolute; right: 42px; top: 58px;
    display: flex; flex-direction: column; align-items: center; gap: 16px;
  }
  .brand-dot { width: 64px; height: 64px; border-radius: 50%; background: var(--brand-blue); }
  .brand-name {
    font-family: "Montserrat", sans-serif; font-weight: 400;
    font-size: 24px; color: var(--ink);
  }
  .person {
    position: absolute; left: 46px; top: 148px;
    font-family: "Roboto", sans-serif; color: var(--ink-soft);
  }
  .person-name { font-weight: 700; font-size: 20px; color: var(--brand-blue); line-height: 1.1; }
  .person-role, .person-quals { font-size: 10.5px; line-height: 1.3; }
  .contacts { list-style: none; margin-top: 12px; }
  .contacts li {
    display: flex; align-items: center; gap: 10px;
    font-size: 13px; line-height: 1.45; color: var(--ink);
  }
  .contacts svg { width: 11px; height: 11px; flex: none; }
</style>
</head>
<body>
<main class="canvas">
  <section class="card card-front" aria-label="Card front">
    <div class="decor" role="img" aria-label="Soft brand gradient in blue and green"></div>
    <h1 class="company">Harbour Lane</h1>
  </section>

  <section class="card card-back" aria-label="Card back">
    <span class="tab tab-left"></span>
    <span class="tab tab-right"></span>

    <div class="brand">
      <span class="brand-dot"></span>
      <span class="brand-name">Harbour Lane</span>
    </div>

    <div class="person">
      <h2 class="person-name">Dara Whelby</h2>
      <p class="person-role">Counsellor &amp; Psychotherapist</p>
      <p class="person-quals">BSc (Psychol.), BA, Dip. (Couns. &amp; Psych.),<br>PG.Cert (CBT), FGTrK, ONRE</p>
      <ul class="contacts">
        <li>
          <svg viewBox="0 0 12 12" aria-hidden="true"><path d="M2 1h2.5l1 2.5-1.5 1a6 6 0 0 0 3.5 3.5l1-1.5L11 7.5V10a1 1 0 0 1-1 1A9 9 0 0 1 1 2a1 1 0 0 1 1-1z" fill="#3aa57a"/></svg>
          0123 555 0190
        </li>
        <li>
          <svg viewBox="0 0 12 12" aria-hidden="true"><rect x="0.5" y="2" width="11" height="8" rx="1" fill="#3aa57a"/><path d="M1 2.5 6 7l5-4.5" stroke="#fff" stroke-width="1" fill="none"/></svg>
          dara.w@HarbourLane.com
        </li>
        <li>
          <svg viewBox="0 0 12 12" aria-hidden="true"><circle cx="6" cy="6" r="5.2" fill="#3aa57a"/><path d="M1 6h10M6 1c-2.4 2.8-2.4 7.2 0 10M6 1c2.4 2.8 2.4 7.2 0 10" stroke="#fff" stroke-width=".8" fill="none"/></svg>
          www.HarbourLane.com
        </li>
      </ul>
    </div>
  </section>
</main>
</body>
</html>
```